Talking Ledger Hour Podcast artwork

Podcast Artwork. Hosted by Marlow Teedquist. Also looking for a clear and distinct font that can be used as a logo for business cards and website. This podcast is a long format, conversation driven podcast about the stories behind cryptocurrencies and blockchain technology. We dive into what's exciting and what's to come and how industries, the internet, and the way we do business is being changed through this new technology. It will be conversation driven rather than tech heavy. Navy or Royal Blue and Hot Pink would be our first choices of colours.

Target Market(s)

Finance, Entertainment, Technology sectors.

Contact Information for Business Card

Marlow Teedquist
Podcast Host
@talkingledger
talkingledgerhour.example
talkingledger@mailnook.example

Logo Text

Talking Ledger Hour Podcast

Font styles to use
Sans Serif

Colors
0455a3
e667a6

Requirements
Must have
• Colours that match the website: talkingledgerhour.example
Nice to have
• A style that matches the website talking ledger hour.com

```html
<!DOCTYPE html>
<html lang="en">
<head>
<meta charset="utf-8">
<title>Talking Ledger Hour Podcast Artwork</title>
<link rel="stylesheet" href="https://fonts.googleapis.com/css2?family=Oswald:wght@700&family=Montserrat:ital,wght@1,700&display=swap">
<style>
  :root {
    --coral: #f0616a;
    --royal-blue: #117bba;
    --paper: #ffffff;
    --mist-blue: #e8f0f7;
    --mist-pink: #fdeeee;
  }
  html, body {
    margin: 0;
    padding: 0;
    overflow: hidden;
    background: var(--paper);
  }
  .artwork {
    position: relative;
    width: 1200px;
    height: 1200px;
    background: var(--paper);
    overflow: hidden;
  }
  .backdrop-tint {
    position: absolute;
    left: 200px;
    top: 200px;
    width: 860px;
    height: 860px;
    border-radius: 50%;
    background: radial-gradient(circle, var(--mist-blue) 0%, var(--mist-pink) 60%, var(--paper) 100%);
    opacity: 0.7;
  }
  .frame {
    position: absolute;
    left: 32px;
    top: 37px;
    width: 1078px;
    height: 1076px;
    border: 29px solid var(--coral);
  }
  .brand-dot {
    position: absolute;
    left: 148px;
    top: 500px;
    width: 270px;
    height: 270px;
    border-radius: 50%;
    background: var(--coral);
  }
  .wordmark {
    position: absolute;
    right: 124px;
    top: 478px;
    margin: 0;
    text-align: right;
    font-family: "Oswald", "Arial Narrow", sans-serif;
    font-weight: 700;
    font-size: 96px;
    line-height: 1.02;
    color: var(--royal-blue);
    letter-spacing: 0.5px;
  }
  .host-name {
    position: absolute;
    right: 124px;
    top: 744px;
    margin: 0;
    font-family: "Montserrat", "Helvetica", sans-serif;
    font-style: italic;
    font-weight: 700;
    font-size: 46px;
    letter-spacing: 1px;
    color: var(--coral);
    text-transform: uppercase;
  }
</style>
</head>
<body>
  <main class="artwork">
    <div class="backdrop-tint" aria-hidden="true"></div>
    <div class="frame" aria-hidden="true"></div>
    <div class="brand-dot" aria-hidden="true"></div>
    <h1 class="wordmark">Talking Ledger<br>Hour</h1>
    <p class="host-name">Marlow Teedquist</p>
  </main>
</body>
</html>
```